Thoroughbred Racing Partnership needs web design

Glimmer of Laurel Partners is a management group who buys horses and races them on both the West and East coasts. The premise of the business is for an investment as little as $500, anyone can be a partner and own a percentage of a horse(s). This is a low cost way of getting involved in the exciting sport of Thoroughbred Racing, without shouldering the heavy financial responsibility. Our target market is mostly males 40+ but we want to include all target markets. We are looking for something very clean and professional, we want to give an image of success. Nothing overly "artsy." I have included the logo in which you can incorporate in the site. Also, the logo colors will be the colors of our "silks." The silks are what the jockey wears and will be an important marketing tool for GOL. We would like a very prominent picture of a racehorse somewhere on the homepage, we want to make it clear that is a website for Horseracing partnerships.

On the top of the site, it should say "Glimmer of Laurel" (on the top)
and below that "Thoroughbred Racing Partnerships." (below that)

The main sections, which should be across the top are:

Home
About Us
Ownership
Stable Roster
News
Contact us

Some of these will have drop down menus.

An example of a competitor website that we like is: www.harrowgatefarm.example
An example of a competitor website that we don't like is: www.paddockvue.example
Updates

Project Deadline Extended
Reason: We have a Board of Directors meeting on the 22nd and we will be making a decision on that day. I'm giving an extension so that all designers are able to submit their designs by the 22nd. Thank you!

Target Market(s)

40+ males

Industry/Entity Type

Business

Requirements
Must have
• our logo must be on the site. We would like at least one bold image of a thoroughbred horse in action. The picture is going to tell the story so it needs to be very eye-catching.

Our slogan should also be included on the website, "Experience the thrill of owning a Racehorse."
Should not have
• cartoons, artsy pictures, pictures of Steeplechase horses or "jumpers." This partnership is for racehorses only, there is not jumping involved with the horses.

```html
<!DOCTYPE html>
<html lang="en">
<head>
<meta charset="utf-8">
<title>Glimmer of Laurel Partners</title>
<link href="https://fonts.googleapis.com/css2?family=PT+Sans:wght@400;700&family=PT+Sans+Narrow:wght@400;700&family=Oswald:wght@500&display=swap" rel="stylesheet">
<style>
:root{
  --navy:#0b4677;
  --blue:#0d5590;
  --blue-dark:#083a66;
  --ink:#3c3c3c;
  --rule:#cfcfcf;
  --footer-top:#0a4c86;
  --footer-bot:#0c5a9a;
  --footer-text:#e6eef7;
}
*{margin:0;padding:0;box-sizing:border-box}
html,body{width:1200px;height:1102px;overflow:hidden}
body{position:relative;font-family:"PT Sans",sans-serif;color:var(--ink);font-size:12.5px;
  background:#9aa4ab}
.backdrop{position:absolute;inset:0;background:linear-gradient(90deg,#7d8990 0%,#c9d0d4 35%,#c4cbcf 65%,#7f8a91 100%)}
.page{position:absolute;left:131px;top:0;width:938px;height:934px;background:#fff}
.abs{position:absolute}
.logo{left:141px;top:18px;display:flex;align-items:center;gap:10px}
.logo .mark{width:34px;height:34px;border-radius:50%;background:var(--navy)}
.logo .name{font-family:"PT Sans",sans-serif;font-weight:700;font-size:40px;color:var(--navy);line-height:1}
.logo .sub{position:absolute;left:0;top:58px;font-weight:700;font-size:26px;color:var(--navy);letter-spacing:1px}
.tagline{left:600px;top:18px;width:280px;text-align:center;font-family:"PT Sans Narrow",sans-serif;font-size:18px;color:#3f6f98;line-height:21px}
.call{left:891px;top:21px;display:flex;gap:10px}
.call .ico{width:34px;height:34px;border-radius:7px;background:linear-gradient(#fafafa,#dcdcdc);border:1px solid #ccc;display:flex;align-items:center;justify-content:center}
.call .lbl{font-weight:700;font-size:13px;color:#333;line-height:14px;margin-top:0}
.call .num{font-family:"PT Sans Narrow",sans-serif;font-weight:700;font-size:20px;color:var(--navy);line-height:22px}
.nav{left:412px;top:77px;width:647px;height:37px;background:linear-gradient(#0e5b98,#0a4a80);display:flex}
.nav a{display:flex;align-items:center;justify-content:center;color:#fff;text-decoration:none;font-weight:700;font-size:14px;border-left:1px solid #2f6fa6;height:100%}
.nav a:first-child{border-left:0;background:#000}
.hero{left:141px;top:121px;width:919px;height:431px;background:linear-gradient(180deg,#6f9a4a 0%,#5c8a3a 30%,#7a6a4a 55%,#6a9a3c 85%,#5e8c36 100%)}
.hero .caption{position:absolute;left:0;top:366px;width:100%;height:55px;background:rgba(20,24,16,.78);display:flex;align-items:center;padding-left:15px}
.hero .caption h1{font-family:"Oswald",sans-serif;font-weight:500;font-size:29px;color:#fff;letter-spacing:-.3px}
.hero .dots{position:absolute;right:19px;top:18px;display:flex;gap:6px}
.hero .dots span{width:19px;height:19px;background:#fff}
.hero .dots span:first-child{background:#3f78a8}
.h2{font-weight:700;font-size:22px;color:var(--navy);line-height:1}
.rule{height:1px;background:var(--rule)}
.photo{left:141px;top:612px;width:187px;height:143px;border:1px solid #ccc;padding:4px;background:#fff}
.photo div{width:100%;height:100%;background:linear-gradient(135deg,#3a2a24,#8a6b55 50%,#2c2a30)}
.intro{left:339px;top:610px;width:392px;font-size:12.5px;line-height:21px;text-align:justify;color:#444}
.more{font-weight:700;font-size:13px;color:var(--navy)}
.news-item{left:779px;width:280px;display:flex;gap:11px}
.date{width:40px;flex:none;text-align:center}
.date b{display:block;height:30px;background:#e4e4e4;font-size:20px;line-height:30px;color:#333}
.date i{display:block;height:14px;background:var(--navy);color:#fff;font-style:normal;font-weight:700;font-size:10px;line-height:14px}
.news-item p{font-size:12px;line-height:17.5px;color:#444}
.news-item strong{color:#333}
.testis{left:141px;top:817px;width:918px;height:88px;border:1px solid #c9c9c9;border-radius:4px;background:#fff}
.quote{width:333px;font-size:12.5px;line-height:18.5px;color:#444}
.quote em{display:block;text-align:right;font-weight:700;margin-top:-6px;color:#333}
.qm{font-family:Georgia,serif;font-size:30px;color:#ccc;line-height:0;vertical-align:-9px;margin-right:4px}
.footer{left:0;top:934px;width:1200px;height:168px;background:linear-gradient(var(--footer-top),var(--footer-bot));border-top:3px solid #0a3f70;color:var(--footer-text)}
.ft{font-weight:700;font-size:17px;color:#fff;letter-spacing:.5px}
.fline{height:1px;background:#4a80b3}
.vsep{width:2px;height:120px;background:linear-gradient(#0a3f72,#185f9c)}
.flink{font-size:12.5px;color:#fff}
.flink::before{content:"»";font-size:9px;color:#9cc0e2;margin-right:5px;vertical-align:1px}
.ftxt{font-size:12.5px;line-height:19px;color:#fff}
.input{left:353px;top:1024px;width:185px;height:23px;background:#fff;border:1px solid #9bb;border-radius:3px;font-size:11.5px;color:#666;padding:4px 9px}
.btn{left:354px;top:1059px;width:77px;height:23px;background:#083460;border:1px solid #3b6e9e;color:#fff;font-weight:700;font-size:13px;text-align:center;line-height:21px}
.social{left:904px;top:992px;display:flex;gap:6px}
.social span{width:27px;height:27px;border-radius:5px;background:#d7e3ef}
</style>
</head>
<body>
<div class="backdrop" role="img" aria-label="Blurred black and white racing photograph background"></div>
<div class="page"></div>

<div class="abs logo"><span class="mark"></span><span class="name">GOL</span><span class="sub">PARTNERS</span></div>
<div class="abs tagline">Glimmer of Laurel<br>Thoroughbred Racing Partnerships</div>
<div class="abs call">
  <div class="ico"><svg width="20" height="20" viewBox="0 0 24 24"><path d="M6.6 10.8a15 15 0 0 0 6.6 6.6l2.2-2.2a1 1 0 0 1 1-.25 11 11 0 0 0 3.6.6 1 1 0 0 1 1 1V20a1 1 0 0 1-1 1A17 17 0 0 1 3 4a1 1 0 0 1 1-1h3.5a1 1 0 0 1 1 1c0 1.25.2 2.45.6 3.6a1 1 0 0 1-.25 1z" fill="#444"/></svg></div>
  <div><div class="lbl">Call Us:</div><div class="num">(123) 456-7890</div></div>
</div>

<nav class="abs nav">
  <a style="width:85px">Home</a><a style="width:108px">About Us</a><a style="width:115px">Ownership</a><a style="width:137px">Stable Roster</a><a style="width:86px">News</a><a style="width:116px">Contact us</a>
</nav>

<div class="abs hero" role="img" aria-label="Thoroughbred racehorses with jockeys galloping on a turf track">
  <div class="caption"><h1>Experience the thrill of owning a Racehorse.</h1>
    <div class="dots"><span></span><span></span><span></span><span></span></div></div>
</div>

<h2 class="abs h2" style="left:141px;top:573px">Welcome to GOL Partners</h2>
<div class="abs rule" style="left:141px;top:602px;width:591px"></div>
<div class="abs photo"><div role="img" aria-label="Partners presenting a trophy plaque"></div></div>
<p class="abs intro">Glimmer of Laurel Partners is a management group who buys horses and races them on both the West and East coasts. The premise of the business is for an investment as little as $500, anyone can be a partner and own a percentage of a horse(s). This is a low cost way of getting involved in the exciting sport of Thoroughbred Racing, without shouldering the heavy financial responsibility.</p>
<div class="abs more" style="left:653px;top:743px">Read More »</div>
<div class="abs" style="left:752px;top:611px;width:2px;height:120px;background:#d8d8d8"></div>

<h2 class="abs h2" style="left:773px;top:573px">Latest News</h2>
<div class="abs rule" style="left:773px;top:602px;width:286px"></div>
<div class="abs news-item" style="top:613px"><div class="date"><b>26</b><i>MAR</i></div><p><strong>Duis aute irure dolor in reprehen</strong><br>voluptate velit esse cillum fugiat nulla pariatur. Excepteur sint occaecat..</p></div>
<div class="abs" style="left:779px;top:671px;width:273px;border-top:1px dotted #ccc"></div>
<div class="abs news-item" style="top:684px"><div class="date"><b>27</b><i>MAR</i></div><p><strong>Duis aute irure dolor in reprehen</strong><br>voluptate velit esse cillum fugiat nulla pariatur. Excepteur sint occaecat..</p></div>
<div class="abs more" style="left:972px;top:743px">Read More »</div>

<div class="abs rule" style="left:141px;top:786px;width:919px"></div>

<div class="abs testis"></div>
<svg class="abs" style="left:143px;top:819px" width="170" height="83" viewBox="0 0 170 83"><path d="M0 0H141L170 41.5 141 83H0Z" fill="#0b4a80"/><text x="77" y="37" text-anchor="middle" fill="#fff" font-family="PT Sans,sans-serif" font-weight="700" font-size="19">Client</text><text x="77" y="58" text-anchor="middle" fill="#fff" font-family="PT Sans,sans-serif" font-weight="700" font-size="19">Testimonials</text></svg>
<div class="abs quote" style="left:338px;top:828px;padding-left:12px;text-indent:-12px"><span class="qm">“</span>Sed diam nonummy nibh euismod tincidunt ut laoreet dolore magna aliquam erat volutpat. Ut wisi enim a mini veniam, quis nostrud exerci tation<em>- Aliquam erat</em></div>
<div class="abs" style="left:689px;top:827px;height:68px;border-left:1px dashed #ccc"></div>
<div class="abs quote" style="left:708px;top:828px;padding-left:12px;text-indent:-12px"><span class="qm">“</span>Sed diam nonummy nibh euismod tincidunt ut laoreet dolore magna aliquam erat volutpat. Ut wisi enim a mini veniam, quis nostrud exerci tation<em>- Aliquam erat</em></div>

<footer class="abs footer"></footer>
<div class="abs ft" style="left:140px;top:944px">Quick Links</div>
<div class="abs fline" style="left:140px;top:971px;width:155px"></div>
<div class="abs flink" style="left:140px;top:984px">Home</div>
<div class="abs flink" style="left:228px;top:984px">News</div>
<div class="abs flink" style="left:140px;top:1007px">About Us</div>
<div class="abs flink" style="left:228px;top:1007px">Contact us</div>
<div class="abs flink" style="left:140px;top:1031px">Ownership</div>
<div class="abs flink" style="left:140px;top:1055px">Stable Roster</div>
<div class="abs vsep" style="left:321px;top:960px"></div>

<div class="abs ft" style="left:352px;top:944px">Newsletter</div>
<div class="abs fline" style="left:352px;top:971px;width:190px"></div>
<div class="abs ftxt" style="left:353px;top:978px;width:200px;line-height:17px">Get the latest updates by entering your email address</div>
<div class="abs input">Email Address</div>
<div class="abs btn">Subscribe</div>
<div class="abs vsep" style="left:567px;top:960px"></div>

<div class="abs ft" style="left:605px;top:944px">Contact Details</div>
<div class="abs fline" style="left:605px;top:971px;width:215px"></div>
<svg class="abs" style="left:606px;top:984px" width="12" height="18" viewBox="0 0 12 18"><path d="M6 0a6 6 0 0 0-6 6c0 4.5 6 12 6 12s6-7.5 6-12a6 6 0 0 0-6-6zm0 8.5A2.5 2.5 0 1 1 6 3.5a2.5 2.5 0 0 1 0 5z" fill="#fff"/></svg>
<div class="abs ftxt" style="left:628px;top:980px;width:200px">Lorem ipsum dolor sit consectetur adipiscing elit.site amet</div>
<svg class="abs" style="left:605px;top:1029px" width="14" height="14" viewBox="0 0 24 24"><path d="M6.6 10.8a15 15 0 0 0 6.6 6.6l2.2-2.2a1 1 0 0 1 1-.25 11 11 0 0 0 3.6.6 1 1 0 0 1 1 1V20a1 1 0 0 1-1 1A17 17 0 0 1 3 4a1 1 0 0 1 1-1h3.5a1 1 0 0 1 1 1c0 1.25.2 2.45.6 3.6a1 1 0 0 1-.25 1z" fill="#fff"/></svg>
<div class="abs ftxt" style="left:628px;top:1027px">(123) 456-7890</div>
<svg class="abs" style="left:605px;top:1055px" width="16" height="11" viewBox="0 0 16 11"><rect x=".5" y=".5" width="15" height="10" fill="none" stroke="#fff"/><path d="M.5.5 8 6.5 15.5.5" fill="none" stroke="#fff"/></svg>
<div class="abs ftxt" style="left:628px;top:1050px">info@golpartners.example</div>
<div class="abs vsep" style="left:848px;top:960px"></div>

<div class="abs ft" style="left:881px;top:944px">Follow Us</div>
<div class="abs fline" style="left:881px;top:971px;width:179px"></div>
<div class="abs social"><span></span><span></span><span></span><span></span></div>
<div class="abs ftxt" style="left:869px;top:1036px;width:200px;text-align:center">Copyright © 2013 Golpartners<br>All Rights Reserved</div>
</body>
</html>
```